Home Staging Company needs business card design

We're a home staging company called Brightly Settled Home Staging. We would like a business card design that includes aqua and gray. Our current logo of house within chair is fine but I find we almost always use the logo in one color. I'll upload images of front and back of our current card and our logo. Note that we have dropped "Solutions" from our company name and don't want to include it on the card.

Target Market(s)

Realtors and homeowners - people interested in selling their homes

Contact Information for Business Card

Marisol Thistlewood
Brightly Settled Home Staging
757-555-0193
www.brightlysettled.com
marisol@brightlysettled.com

Font styles to use
Serif
Script

Requirements
Must have
• My logo and contact details
• UPDATE***
• I forgot to say that the company name should be included on the front of the card somehow.

```html
<!DOCTYPE html>
<html lang="en">
<head>
<meta charset="utf-8">
<title>Brightly Settled Home Staging — Business Card</title>
<link rel="stylesheet" href="https://fonts.googleapis.com/css2?family=Playfair+Display:wght@700&family=Hind:wght@400;500&display=swap">
<style>
  :root {
    --backdrop: #d9dadb;
    --card: #262627;
    --aqua: #56b8c4;
    --ink-light: #f2f2f2;
    --ink-muted: #b9b9b9;
  }
  * { box-sizing: border-box; margin: 0; padding: 0; }
  html, body { width: 799px; height: 1200px; overflow: hidden; }
  body {
    background: var(--backdrop);
    display: flex;
    flex-direction: column;
    align-items: center;
    justify-content: center;
    gap: 90px;
    font-family: "Hind", Arial, sans-serif;
  }
  .card {
    position: relative;
    width: 640px;
    height: 366px;
    background: var(--card);
    border-radius: 4px;
    overflow: hidden;
    box-shadow: 0 10px 24px rgba(0,0,0,0.25);
  }
  .brand {
    display: flex;
    align-items: center;
    font-family: "Playfair Display", Georgia, serif;
    font-weight: 700;
    white-space: nowrap;
    line-height: 1;
  }

  /* Front */
  .card--front {
    display: flex;
    align-items: center;
    justify-content: center;
  }
  .card--front .brand {
    flex-direction: column;
    gap: 22px;
    font-size: 32px;
    color: var(--aqua);
  }
  .brand__mark {
    width: 150px;
    height: 150px;
    border-radius: 50%;
    background: var(--aqua);
    flex: none;
  }

  /* Back */
  .card--back .brand {
    position: absolute;
    left: 40px;
    top: 40px;
    font-size: 26px;
    color: var(--ink-light);
  }
  .contact {
    position: absolute;
    left: 40px;
    top: 150px;
  }
  .contact__name {
    color: var(--ink-light);
    font-size: 24px;
    font-weight: 500;
    line-height: 1;
  }
  .contact__title {
    color: var(--ink-muted);
    font-size: 14px;
    margin-top: 8px;
  }
  .contact__list { list-style: none; margin-top: 22px; }
  .contact__item {
    display: flex;
    align-items: center;
    gap: 10px;
    color: var(--ink-light);
    font-size: 15px;
    line-height: 1.7;
  }
  .contact__icon { width: 13px; height: 13px; fill: var(--aqua); flex: none; }
  .accent-disc {
    position: absolute;
    right: -90px;
    bottom: -170px;
    width: 400px;
    height: 400px;
    border-radius: 50%;
    background: var(--aqua);
  }
</style>
</head>
<body>
  <section class="card card--front">
    <div class="brand">
      <span class="brand__mark"></span>
      <span class="brand__name">Brightly Settled Home Staging</span>
    </div>
  </section>

  <section class="card card--back">
    <div class="brand"><span class="brand__name">Brightly Settled Home Staging</span></div>
    <div class="contact">
      <p class="contact__name">Marisol Thistlewood</p>
      <p class="contact__title">Managing Director</p>
      <ul class="contact__list">
        <li class="contact__item">
          <svg class="contact__icon" viewBox="0 0 16 16"><path d="M3 1h3l1.5 4-2 1.3a9 9 0 0 0 4.2 4.2L11 8.5l4 1.5v3a2 2 0 0 1-2 2A13 13 0 0 1 1 3a2 2 0 0 1 2-2z"/></svg>
          757-555-0193
        </li>
        <li class="contact__item">
          <svg class="contact__icon" viewBox="0 0 16 16"><path d="M8 1a7 7 0 1 0 0 14A7 7 0 0 0 8 1zm0 1.5c.9 1 1.5 2.5 1.7 4.5H6.3C6.5 5 7.1 3.5 8 2.5zM2.6 7h2.2c.1-1.6.5-3 1.1-4A5.5 5.5 0 0 0 2.6 7zm0 2a5.5 5.5 0 0 0 3.3 4c-.6-1-1-2.4-1.1-4zm3.7 0h3.4c-.2 2-.8 3.5-1.7 4.5C7.1 12.5 6.5 11 6.3 9zm4.9 0c-.1 1.6-.5 3-1.1 4a5.5 5.5 0 0 0 3.3-4zm2.2-2a5.5 5.5 0 0 0-3.3-4c.6 1 1 2.4 1.1 4z"/></svg>
          www.brightlysettled.com
        </li>
        <li class="contact__item">
          <svg class="contact__icon" viewBox="0 0 16 16"><path d="M1 3h14v10H1zm1.5 1.5v.4L8 9l5.5-4.1v-.4zm0 2.3V11.5h11V6.8L8 10.9z"/></svg>
          marisol@brightlysettled.com
        </li>
      </ul>
    </div>
    <div class="accent-disc"></div>
  </section>
</body>
</html>
```